Product Design for VelaMira

Design Brief for VelaMira Product Packaging

Objective:
Create a cohesive, elegant, and brand-consistent packaging design for the VelaMira product line. The signature visual theme should reflect luxury, femininity, and clean beauty values.

---

🎨 Core Design Direction

Unified Aesthetic: All containers must prominently feature the floral pattern shown in "Pattern Reference: Image 3". This design serves as the brand's signature aesthetic and must be applied uniformly across all SKUs.

Brand Logo Placement: The VelaMira logo (provided) should be clearly visible and harmoniously integrated into the patterned background.

Color Palette: Base colors should complement the brand’s primary palette: black, blush pink, and white.

---

🧴 Product-Specific Packaging Specifications

1. Mascara

Bottle Type: Sleek mascara tube with a wand applicator

Capacity: 5ml

Design: Use floral pattern from Pattern Reference Image 3. Ensure the pattern does not obstruct the readability of the logo or any regulatory text.

2. Eyebrow Growth Serum

Bottle Type: 5ml tube with fine-tip brush applicator

Capacity: 5ml

Design: Same floral pattern, scaled and applied proportionally to match the mascara for consistency

3. Eyelash Growth Serum

Bottle Type: 5ml tube with fine-tip brush (similar to the eyebrow serum, unless otherwise advised)

Capacity: 5ml

Design: Identical styling to maintain unity across lash & brow products

4. Anti-Aging Serum or Lotion

Bottle Type: 30ml airless pump bottle (preferred for hygiene and product stability)

Capacity: 30ml

Design: Apply floral pattern from Pattern Reference and scale appropriately for larger surface area

5. Hair Growth Spray

Bottle Type: 50ml fine mist spray bottle

Capacity: 50ml

Design: Pattern applied and scaled for taller profile; maintain visual harmony with skincare line

---

📦 Additional Notes

Please ensure packaging aligns with clean beauty standards (no overly glossy plastic finishes, avoid excessive secondary packaging unless sustainable).

Materials should be eco-conscious where possible.

If embossing, foil stamping, or UV finishing is available for logo accents, please suggest options.

```html
<!DOCTYPE html>
<html lang="en">
<head>
<meta charset="utf-8">
<title>VelaMira Anti Aging Serum Label</title>
<link rel="stylesheet" href="https://fonts.googleapis.com/css2?family=Playfair+Display:wght@500&family=Outfit:wght@500&display=swap">
<style>
  :root {
    --canvas: #ffffff;
    --ink: #141414;
    --blush: #f7d6d3;
    --blush-soft: #fbeceb;
    --blush-pale: #fdf6f5;
    --floral-line: #e0a194;
    --floral-mid: #efc3ba;
    --floral-light: #fbefec;
    --gold-dark: #a8741a;
    --gold-mid: #d4b033;
    --gold-light: #f6ee95;
  }
  * { margin: 0; padding: 0; box-sizing: border-box; }
  html, body {
    width: 1200px;
    height: 981px;
    overflow: hidden;
    background: var(--canvas);
  }
  .canvas {
    position: relative;
    width: 1200px;
    height: 981px;
  }
  .label {
    position: absolute;
    left: 150px;
    top: 135px;
    width: 900px;
    height: 710px;
    box-shadow: 0 6px 18px rgba(0, 0, 0, 0.12);
    overflow: hidden;
  }
  .label__pattern {
    position: absolute;
    left: 0; top: 0;
    width: 100%;
    height: 305px;
    background:
      radial-gradient(ellipse 170px 140px at 44% 52%, var(--floral-mid) 0%, transparent 100%),
      radial-gradient(ellipse 150px 120px at 77% 68%, var(--floral-mid) 0%, transparent 100%),
      radial-gradient(ellipse 140px 160px at 10% 70%, var(--floral-mid) 0%, transparent 100%),
      radial-gradient(ellipse 150px 110px at 90% 20%, var(--floral-mid) 0%, transparent 100%),
      linear-gradient(135deg, var(--floral-light) 0%, #f6d8d1 50%, var(--floral-light) 100%);
  }
  .label__foil {
    position: absolute;
    left: 0; top: 305px;
    width: 100%;
    height: 19px;
    background: linear-gradient(90deg,
      var(--gold-dark) 0%, var(--gold-mid) 18%, var(--gold-light) 38%,
      var(--gold-mid) 58%, var(--gold-dark) 70%, var(--gold-mid) 86%, var(--gold-light) 100%);
  }
  .label__panel {
    position: absolute;
    left: 0; top: 324px;
    width: 100%;
    height: 386px;
    background:
      radial-gradient(ellipse at 0% 40%, var(--blush) 0, transparent 45%),
      radial-gradient(ellipse at 100% 30%, var(--blush) 0, transparent 40%),
      radial-gradient(ellipse at 90% 100%, var(--blush) 0, transparent 45%),
      radial-gradient(ellipse at 20% 100%, var(--blush-soft) 0, transparent 50%),
      var(--blush-pale);
  }
  .brand-name {
    position: absolute;
    left: 0; right: 0;
    top: 384px;
    text-align: center;
    font-family: "Playfair Display", serif;
    font-weight: 500;
    font-size: 100px;
    line-height: 118px;
    color: var(--ink);
    letter-spacing: 1px;
  }
  .product-name {
    position: absolute;
    left: 0; right: 0;
    top: 536px;
    text-align: center;
    font-family: "Outfit", sans-serif;
    font-weight: 500;
    font-size: 40px;
    line-height: 48px;
    color: var(--ink);
  }
  .product-volume {
    position: absolute;
    left: 0; right: 0;
    top: 638px;
    text-align: center;
    font-family: "Outfit", sans-serif;
    font-weight: 500;
    font-size: 35px;
    line-height: 42px;
    color: var(--ink);
  }
</style>
</head>
<body>
  <main class="canvas">
    <section class="label">
      <div class="label__pattern" role="img" aria-label="Blush line-art floral pattern of peonies, blossoms and leafy sprigs"></div>
      <div class="label__foil"></div>
      <div class="label__panel"></div>
      <h1 class="brand-name">VelaMira</h1>
      <p class="product-name">Anti Aging Serum</p>
      <p class="product-volume">30ml</p>
    </section>
  </main>
</body>
</html>
```